Local Roofing Company Billboard Design

We need a billboard design for an 8' x 32' billboard. This billboard would need to be easily readable and stand out well.
I have uploaded a design that we like - simple, readable, and gets the point across. We do NOT want the $1000 off offer included.
We are looking for a black background with white copy so it will stand out. We want the following on the billboard:
Brindlewick Roofing logo
brindlewick-roofing.example (optional)
555.214.7730 (mandatory)
Photo is optional, depends on how it all lays out
Production file must comply with layout requirements (uploaded).
Target Market(s)
Homeowners
Font styles to use
Other font styles liked:
- match font from logo
Colors
Designer to choose colors to be used in the design.
Requirements
Must have
- Black background, white copy, logo must be large and legible. Colors used must match our logo colors.

```html
<!DOCTYPE html>
<html lang="en">
<head>
<meta charset="utf-8">
<title>Brindlewick Roofing Billboard</title>
<link rel="stylesheet" href="https://fonts.googleapis.com/css2?family=Montserrat:wght@500;700;800&family=Oswald:wght@500&display=swap">
<style>
  :root {
    --orange: #e4561e;
    --ink: #0b0b0b;
    --paper: #ffffff;
    --stage: #ffffff;
  }
  * { margin: 0; padding: 0; box-sizing: border-box; }
  html, body {
    width: 1200px;
    height: 1051px;
    overflow: hidden;
    background: var(--stage);
  }
  .billboard {
    position: absolute;
    left: 40px;
    top: 385px;
    width: 1120px;
    height: 280px;
    background: var(--paper);
    box-shadow: 0 10px 40px rgba(0,0,0,0.18);
    overflow: hidden;
  }
  .bands {
    position: absolute;
    inset: 0;
  }
  .brand-name {
    position: absolute;
    left: 36px;
    top: 42px;
    font-family: "Montserrat", sans-serif;
    font-weight: 800;
    font-size: 54px;
    line-height: 1.02;
    color: var(--ink);
    letter-spacing: -0.5px;
  }
  .headline {
    position: absolute;
    right: 22px;
    top: 26px;
    text-align: right;
    font-family: "Montserrat", sans-serif;
    font-weight: 700;
    font-size: 52px;
    line-height: 1.2;
    color: var(--orange);
    letter-spacing: -0.5px;
  }
  .website {
    position: absolute;
    left: 30px;
    top: 227px;
    display: flex;
    align-items: center;
    gap: 14px;
    font-family: "Montserrat", sans-serif;
    font-weight: 500;
    font-size: 19px;
    letter-spacing: 0.3px;
    color: var(--paper);
    white-space: nowrap;
  }
  .website svg { width: 32px; height: 25px; flex: none; }
  .phone {
    position: absolute;
    left: 516px;
    top: 178px;
    display: flex;
    align-items: center;
    gap: 28px;
  }
  .phone svg { width: 62px; height: 62px; }
  .phone-number {
    font-family: "Oswald", sans-serif;
    font-weight: 500;
    font-size: 88px;
    line-height: 1;
    color: var(--paper);
    letter-spacing: 1px;
  }
  .phone-number .dash { color: var(--orange); }
</style>
</head>
<body>
  <div class="billboard">
    <svg class="bands" viewBox="0 0 1120 280" aria-hidden="true">
      <polygon points="0,205 470,205 416,280 0,280" fill="var(--ink)"/>
      <polygon points="513,161 1120,161 1120,280 426,280" fill="var(--ink)"/>
    </svg>

    <div class="brand-name">Brindlewick<br>Roofing</div>

    <div class="headline">LOCAL EXPERTS,<br>TRUSTED ROOFING</div>

    <div class="website">
      <svg viewBox="0 0 36 28" aria-hidden="true">
        <rect x="5" y="2" width="26" height="18" rx="1.5" fill="none" stroke="var(--orange)" stroke-width="3.5"/>
        <rect x="0" y="22" width="36" height="5" rx="1.5" fill="var(--orange)"/>
      </svg>
      <span>Brindlewick-Roofing.example</span>
    </div>

    <div class="phone">
      <svg viewBox="0 0 64 64" aria-hidden="true">
        <path d="M14 6 L24 18 C26 21 25 24 22 26 L19 28 C22 36 28 42 36 45 L38 42 C40 39 43 38 46 40 L58 50 C60 52 60 55 58 57 L53 61 C49 64 42 63 34 59 C22 53 11 42 5 30 C1 22 0 15 3 11 L7 6 C9 4 12 4 14 6 Z" fill="var(--orange)"/>
        <path d="M36 22 A8 8 0 0 1 42 28" fill="none" stroke="var(--orange)" stroke-width="3.5" stroke-linecap="round"/>
        <path d="M38 12 A18 18 0 0 1 52 26" fill="none" stroke="var(--orange)" stroke-width="3.5" stroke-linecap="round"/>
      </svg>
      <div class="phone-number">555<span class="dash">-</span>214<span class="dash">-</span>7730</div>
    </div>
  </div>
</body>
</html>
```